Visitenkarten
Zielgruppe
Wir handeln und restaurieren (mit) sehr hochwertigen Fahrzeugen (Oldtimier/Supercars) bis in den Bereich von mehreren Millionen Euro. Die Zielgruppe sind potentielle Käufer im sehr gehobenen Premium Segment.
Aufgabenstellung
Eine Visitenkarte im Idealfall mit dem schwarzen Logo soll erstellt werden. Standardformat oder ein kreatives, aber praktikables Format. Ziel ist eine sehr hochwertige, geprägte Visitenkarte. Frontseite das Vintage Crest Logo, Rückseite einmal: Markus Heldorf, Owner, Phone +436708216473, Email Sales@vintage-crest.com Salzburg Dobrovnik (generisch anpassbare Adresse)

```html
<!DOCTYPE html>
<html lang="de">
<head>
<meta charset="utf-8">
<title>Visitenkarte – Vintage Crest</title>
<link href="https://fonts.googleapis.com/css2?family=Cinzel:wght@400;500&display=swap" rel="stylesheet">
<style>
  :root {
    --backdrop: #d9d9d9;
    --card: #f7f7f6;
    --ink: #2a2526;
    --ink-soft: #3a3536;
  }
  html, body {
    margin: 0;
    padding: 0;
    width: 1200px;
    height: 1200px;
    overflow: hidden;
    background: var(--backdrop);
  }
  .canvas {
    position: relative;
    width: 1200px;
    height: 1200px;
  }
  .business-card {
    position: absolute;
    left: 100px;
    top: 277px;
    width: 1000px;
    height: 646px;
    background: var(--card);
    font-family: "Cinzel", serif;
    color: var(--ink);
    box-shadow: 0 2px 10px rgba(0, 0, 0, 0.08);
  }
  .brand {
    position: absolute;
    right: 106px;
    top: 120px;
    display: flex;
    align-items: center;
    gap: 12px;
  }
  .brand-dot {
    width: 14px;
    height: 14px;
    border-radius: 50%;
    background: var(--ink);
  }
  .brand-name {
    font-size: 26px;
    font-weight: 400;
    letter-spacing: 0.04em;
    color: var(--ink);
  }
  .person {
    position: absolute;
    left: 92px;
    top: 315px;
  }
  .person-name {
    margin: 0;
    font-size: 46px;
    font-weight: 400;
    letter-spacing: 0.03em;
    line-height: 1;
    color: var(--ink);
  }
  .person-role {
    margin: 22px 0 0;
    font-size: 23px;
    letter-spacing: 0.04em;
    color: var(--ink-soft);
  }
  .contact {
    position: absolute;
    left: 92px;
    top: 490px;
    font-size: 25px;
    line-height: 42px;
    letter-spacing: 0.02em;
    color: var(--ink);
  }
  .contact p { margin: 0; }
</style>
</head>
<body>
<main class="canvas">
  <section class="business-card" aria-label="Visitenkarte Rückseite">
    <div class="brand">
      <span class="brand-dot"></span>
      <span class="brand-name">Vintage Crest</span>
    </div>
    <div class="person">
      <h1 class="person-name">Markus Heldorf</h1>
      <p class="person-role">Owner</p>
    </div>
    <div class="contact">
      <p class="contact-phone">+436708216473</p>
      <p class="contact-email">Sales@vintage-crest.com</p>
    </div>
  </section>
</main>
</body>
</html>
```